Webdesign für Industrieanlagenbau-Unternehmen
Zielgruppe
Die KLR services GmbH ist ein ein österreichisches, eigentümergeführtes Industrieanlagenbau-Unternehmen mit Niederlassungen an derzeit 2 Standorten (Traiskirchen/NÖ und Hallein/Sbg) und ist in den Geschäftsfeldern Industrieanlagenbau, Reinraumtechnik und Sondermaschinenbau - sowie im Projekt- und Behördenmanagement tätig.
Die KLR services GmbH unterstützt ihre B2B-Kunden bei der Umsetzung von Engineering-Projekten in der Hightech-, Elektronik- und Prozessindustrie.
Unsere Kernkompetenzen sind Konzepterstellung, 3D-Planung, Konstruktion, Design und Montage von Prozessanlagen und Reinräumen, eine eigene Fertigung und Prototypenbau in unserer „Werkhalle Quellbach“ sowie die Abwicklung des Behörden-Managements wie z.B. Einreichverfahren nach Gewerbeordnung.
Langjährige und dauerhafte Geschäftsbeziehungen zu unseren Kunden stehen bei uns im Vordergrund.
Zielsgruppe der neuen website:
„Visitenkarte“ der KLR services GmbH
potentielle Mitarbeiter („Employer Branding“), Ingenieure/Projektmanager (WI-Maschinenbau, Elektro- und Prozesstechnik), Mechatroniker, Schlosser, Elektriker
B2B Kunden aus Bereichen Mikroelektronik-Fertigung, chemische Industrie, Lebensmittel- und Pharmaproduktion
Bestandskunden (Stakeholder des „Buying Centers“ bei Kunden)
Neukunden „eingeschränkt“ (dzt. Keine aktive Kundenakquise via web geplant)
Aufgabenstellung
Allgemeine Anforderungen an die neue website:
Ziel sind eher „schlanke“ Texte & Design (vgl. https://www.varnhold-gruppe.com/de/)
Produkt- und Leistungsspezifisches Bildmaterial sollen hauptsächlich KLR-eigene Fotos und Videos sein (Stock-Fotos nur für Allgemeine Bilder). Beispielhaftes Bildmaterial (sollte durch KLR Mitarbeiter dann im CMS einfach ausgetauscht werden können) in diesen Unterlagen
CMS (Content Management System) zur Administration durch KLR Mitarbeiter
Hosting auf europäischen ServernServern (z.B. https://serverkiste-demo.com/, https://www.datenfeld-demo.com, https://www.rechenhof-demo.de, https://www.netzquelle-demo.com/, https://www.zuvo-demo.at)
Basierend auf weitverbreiteten open-Source Systemen (z.B. Wordpress , Joomla, TYPO3)
Responsive Webdesign – eine Website für alle Geräte (PC, Tablet, Smartphone) und alle gängigen Browser (Chrome, Edge, Safari, Firefox, Opera, Internet Explorer)
Google Pagespeed mind. 85 Punkte, GTmetrix Grade > 80%
Sicherheitszertifikat (SSL-Zertifikat)
Sprache – Deutsch, Englisch
E-Commerce-Gesetz (ECG) & DSGVO konform (Cookie Disclaimer Standard „nur notwendige“)
Impressum
AGB - Allgemeine Lieferungs- und Zahlungsbedingungen
Sitemap
Vollständige Rechte an der website (Design, Inhalt etc.) bei KLR services GmbH
Einbettung von Text, Fotos und Videos durch KLR Mitarbeiter
Hinzufügen von Menü-Unterpunkten durch KLR Mitarbeiter

```html
<!DOCTYPE html>
<html lang="de">
<head>
<meta charset="utf-8">
<title>KLR services GmbH – Industrieanlagenbau</title>
<link href="https://fonts.googleapis.com/css2?family=Lato:wght@300;400;700;900&display=swap" rel="stylesheet">
<style>
:root{
  --red:#e3231f;
  --blue:#2a67b0;
  --blue-dark:#1d4f94;
  --title-blue:#2c5a9c;
  --text:#444;
  --grey:#f1f1f1;
  --grey-light:#f7f7f7;
  --white:#fff;
}
*{box-sizing:border-box;margin:0;padding:0}
html,body{width:1200px;height:2925px;overflow:hidden;background:var(--white);font-family:'Lato',sans-serif;color:var(--text)}
.page{position:relative;width:1200px;height:2925px}
.abs{position:absolute}

.header{top:0;left:0;width:1200px;height:58px;background:var(--white);z-index:3}
.brand{position:absolute;left:161px;top:8px;display:flex;align-items:center;gap:8px}
.brand-square{width:14px;height:14px;background:var(--red)}
.brand-name{font-weight:900;font-size:30px;color:var(--red);letter-spacing:1px;line-height:1}
.brand-sub{font-size:7px;font-weight:700;color:#888;letter-spacing:.5px;margin-top:2px}
.langs{position:absolute;right:162px;top:19px;display:flex;gap:10px}

.hero{top:58px;left:0;width:1200px;height:523px}
.nav{top:58px;left:161px;width:876px;height:38px;background:var(--red);z-index:4}
.nav a{position:absolute;top:0;line-height:38px;color:var(--white);text-decoration:none;font-size:12.5px;font-weight:700;transform:translateX(-50%);white-space:nowrap}
.hero-title{top:360px;left:0;width:1200px;text-align:center;color:var(--white);font-size:62px;font-weight:300;letter-spacing:-1.5px}
.hero-title b{font-weight:900}
.dots{top:486px;left:545px;display:flex;gap:4px}
.dots span{width:19px;height:3px;background:var(--white)}
.dots span:first-child{background:var(--red)}

.section-title{left:0;width:1200px;text-align:center;font-weight:300;font-size:34px;color:var(--title-blue)}
.section-title.red{color:var(--red)}

.about-mark{left:162px;top:698px;width:124px;height:165px;display:flex;align-items:center;justify-content:center;gap:8px}
.about-mark .brand-name{font-size:40px}
.about-text{left:332px;top:699px;width:707px;font-size:12.5px;line-height:19.5px;text-align:justify;color:#555;hyphens:auto}
.about-text p+p{margin-top:19.5px}

.card{position:absolute;width:419px}
.card .photo{height:184px;width:419px}
.card h3{font-weight:400;font-size:19px;color:var(--red);margin:12px 0 4px -3px}
.card p{font-size:12px;line-height:16px;color:#666;width:420px;margin-left:-3px}

.career{top:1859px;left:0;width:1200px;height:368px;
  background:
    radial-gradient(ellipse 190px 230px at 870px 130px,rgba(214,178,150,.95),rgba(214,178,150,.55) 40%,rgba(214,178,150,0) 75%),
    radial-gradient(ellipse 240px 200px at 870px 330px,rgba(26,52,104,.95),rgba(26,52,104,0) 80%),
    radial-gradient(ellipse 180px 300px at 1130px 150px,rgba(190,210,232,.85),rgba(190,210,232,0) 80%),
    linear-gradient(90deg,#225aa3 0%,#2a67b0 50%,#3c74b8 70%,#6c97c9 100%)}
.career-title{top:1942px;left:160px;font-size:34px;font-weight:300;color:var(--white)}
.career-text{top:1995px;left:160px;width:502px;font-size:12.5px;line-height:19.5px;color:var(--white);hyphens:auto}
.career-btn{top:2096px;left:160px;width:185px;height:36px;border:2px solid var(--white);color:var(--white);font-size:13px;line-height:32px;text-align:center}

.gallery{top:2356px;left:161px;width:876px;height:388px;display:grid;grid-template-columns:repeat(3,1fr);grid-template-rows:repeat(2,1fr);gap:1px;background:var(--white)}

.footer{top:2795px;left:0;width:1200px;height:74px;background:var(--grey)}
.footer .brand{top:20px;left:164px}
.footer-links{position:absolute;right:161px;top:30px;display:flex;gap:15px;font-size:11.5px;color:#555}
.copyright{top:2869px;left:0;width:1200px;height:56px;background:var(--grey-light);text-align:center;font-size:11px;line-height:56px;color:#555}
</style>
</head>
<body>
<div class="page">

  <header class="header abs">
    <div class="brand">
      <div class="brand-square"></div>
      <div>
        <div class="brand-name">KLR</div>
        <div class="brand-sub">KLR SERVICES GMBH</div>
      </div>
    </div>
    <div class="langs">
      <svg width="16" height="11" viewBox="0 0 16 11" aria-label="English"><rect width="16" height="11" fill="#1f3f8c"/><rect x="6.5" width="3" height="11" fill="#fff"/><rect y="4" width="16" height="3" fill="#fff"/><rect x="7.2" width="1.6" height="11" fill="#d52b1e"/><rect y="4.7" width="16" height="1.6" fill="#d52b1e"/></svg>
      <svg width="16" height="11" viewBox="0 0 16 11" aria-label="Deutsch"><rect width="16" height="3.7" fill="#000"/><rect y="3.7" width="16" height="3.6" fill="#dd0000"/><rect y="7.3" width="16" height="3.7" fill="#ffce00"/></svg>
    </div>
  </header>

  <svg class="hero abs" width="1200" height="523" viewBox="0 0 1200 523" role="img" aria-label="Industrieanlage mit Rohrleitungen, blau eingefärbt">
    <defs>
      <linearGradient id="heroBase" x1="0" y1="0" x2="1" y2="1">
        <stop offset="0" stop-color="#1a4f98"/>
        <stop offset=".5" stop-color="#2d6cb8"/>
        <stop offset="1" stop-color="#1d58a3"/>
      </linearGradient>
      <radialGradient id="heroGlowA" cx=".42" cy=".35" r=".35">
        <stop offset="0" stop-color="#8cb4e2" stop-opacity=".55"/>
        <stop offset="1" stop-color="#8cb4e2" stop-opacity="0"/>
      </radialGradient>
      <radialGradient id="heroGlowB" cx=".72" cy=".25" r=".3">
        <stop offset="0" stop-color="#7aa6da" stop-opacity=".45"/>
        <stop offset="1" stop-color="#7aa6da" stop-opacity="0"/>
      </radialGradient>
      <radialGradient id="heroShade" cx=".1" cy=".6" r=".4">
        <stop offset="0" stop-color="#123c78" stop-opacity=".6"/>
        <stop offset="1" stop-color="#123c78" stop-opacity="0"/>
      </radialGradient>
      <clipPath id="heroClip"><polygon points="0,0 1200,0 1200,419 600,523 0,419"/></clipPath>
    </defs>
    <g clip-path="url(#heroClip)">
      <rect width="1200" height="523" fill="url(#heroBase)"/>
      <rect width="1200" height="523" fill="url(#heroShade)"/>
      <rect width="1200" height="523" fill="url(#heroGlowA)"/>
      <rect width="1200" height="523" fill="url(#heroGlowB)"/>
    </g>
  </svg>

  <nav class="nav abs">
    <a style="left:109px">HOME-KLR</a>
    <a style="left:263px">LEISTUNGEN</a>
    <a style="left:430px">JOBS/KARRIERE</a>
    <a style="left:611px">KUNDEN-PORTAL</a>
    <a style="left:773px">KONTAKT</a>
  </nav>

  <h1 class="hero-title abs">Wir <b>bauen</b> Ihre <b>Anlagen</b></h1>
  <div class="dots abs"><span></span><span></span><span></span><span></span><span></span></div>

  <h2 class="section-title abs" style="top:636px">Wer wir sind</h2>
  <div class="about-mark abs">
    <div class="brand-square"></div>
    <div class="brand-name">KLR</div>
  </div>
  <div class="about-text abs">
    <p>Die KLR servicesGmbH ist ein österreichisches Industrieanlagenbau-Unternehmen und unterstützt Sie bei der Umsetzung von Engineering-Projekten in der Hightech-, Elektronik-und Prozessindustrie.</p>
    <p>Unsere Kernkompetenzen sind Konzepterstellung, 3D-Planung, Konstruktion, Design und Montage von Prozessanlagen und Reinräumen.</p>
    <p>Wir betreiben eine eigene Fertigung und Prototypenbau in unserer „Werkhalle Quellbach“ und unterhalten einen eigenen Fuhrpark für unsere Montageteams.</p>
  </div>

  <h2 class="section-title abs" style="top:903px">Leistungen</h2>

  <div class="card" style="left:161px;top:974px">
    <div class="photo" role="img" aria-label="Produktionshalle mit Anlagen" style="background:radial-gradient(ellipse at 50% 20%,#d9dcdf 0%,rgba(217,220,223,0) 55%),linear-gradient(180deg,#6e7174 0%,#8e9093 35%,#6a5d51 75%,#4a423b 100%)"></div>
    <h3>Industrieanlagenbau</h3>
    <p>Duis aute irure dolor in reprehenderit in voluptate velit esse cillum dolore eu fugiat nulla pariatur.</p>
  </div>
  <div class="card" style="left:620px;top:974px">
    <div class="photo" role="img" aria-label="3D-Planung eines Reinraums" style="background:linear-gradient(180deg,#fafafa 0%,#9ea3a6 30%,#7f8a84 60%,#e8eaea 80%,#cfd3d4 100%);border:1px solid #bbb"></div>
    <h3 style="margin-top:14px">Reinraumtechnik</h3>
    <p>Duis aute irure dolor in reprehenderit in voluptate velit esse cillum dolore eu fugiat nulla pariatur.</p>
  </div>

  <div class="card" style="left:161px;top:1267px">
    <div class="photo" role="img" aria-label="Sondermaschine in der Werkhalle" style="background:radial-gradient(ellipse at 50% 50%,#4b6a8f 0%,rgba(75,106,143,0) 45%),linear-gradient(90deg,#d9c3c8 0%,#9a8c78 15%,#7b7469 50%,#a3946f 80%,#c46a3c 100%)"></div>
    <h3>Sondermaschinenbau</h3>
    <p>Duis aute irure dolor in reprehenderit in voluptate velit esse cillum dolore eu fugiat nulla pariatur.</p>
  </div>
  <div class="card" style="left:620px;top:1267px">
    <div class="photo" role="img" aria-label="Gasversorgungsanlage mit Kran vor Gebäude" style="background:linear-gradient(180deg,#2c64bd 0%,#6f9bd6 40%,#c9d3db 62%,#9aa08f 80%,#7e8d4e 100%)"></div>
    <h3>Gasversorgungsanlagen</h3>
    <p>Duis aute irure dolor in reprehenderit in voluptate velit esse cillum dolore eu fugiat nulla pariatur.</p>
  </div>

  <div class="card" style="left:161px;top:1564px">
    <div class="photo" role="img" aria-label="Techniker an einer Bohrmaschine" style="background:radial-gradient(ellipse at 62% 15%,#e08a2a 0%,rgba(224,138,42,0) 18%),linear-gradient(90deg,#2c2e31 0%,#6b6d70 30%,#9c9ea0 50%,#55585c 75%,#3a3c40 100%)"></div>
    <h3 style="margin-top:8px">Projekt-Management</h3>
    <p>Duis aute irure dolor in reprehenderit in voluptate velit esse cillum dolore eu fugiat nulla pariatur.</p>
  </div>
  <div class="card" style="left:620px;top:1564px">
    <div class="photo" role="img" aria-label="Schweißarbeiten mit Funkenflug" style="background:radial-gradient(ellipse at 62% 72%,#cfe0ff 0%,#4d78d8 12%,rgba(40,60,140,0) 40%),linear-gradient(90deg,#b8862f 0%,#8a5e22 25%,#2a2620 55%,#15213f 100%)"></div>
    <h3 style="margin-top:3px">Behörden-Management</h3>
    <p>Duis aute irure dolor in reprehenderit in voluptate velit esse cillum dolore eu fugiat nulla pariatur.</p>
  </div>

  <section class="career abs" role="img" aria-label="Mitarbeiter im Anzug mit verschränkten Armen vor blauem Hintergrund"></section>
  <h2 class="career-title abs">Karriere with KLR</h2>
  <p class="career-text abs">Lorem ipsum dolor sit amet, consectetur adipiscing elit, sed do eiusmod tempor incididunt ut labore et dolore magna aliqua. Ut enim ad minim veniam, quis nostrud exercitation ullamco laboris nisi ut aliquip ex ea commodo consequat. Duis aute irure dolor in reprehenderit in voluptate velit esse cillum dolore eu fugiat nulla pariatur.</p>
  <div class="career-btn abs">Aktuelle Stellenangebote</div>

  <h2 class="section-title red abs" style="top:2282px">Galerie</h2>
  <div class="gallery abs">
    <div role="img" aria-label="Hand mit Tablet und leuchtendem Cloud-Symbol" style="background:radial-gradient(circle at 50% 45%,#7fb4f0 0%,#2f6cc4 20%,#0c1f45 65%,#081634 100%)"></div>
    <div role="img" aria-label="Geschäftsleute mit Diagrammen am Tablet" style="background:linear-gradient(125deg,#1d2f52 0%,#3b5680 30%,#c6d0dd 55%,#eef1f4 80%,#d9dde2 100%)"></div>
    <div role="img" aria-label="Auswertung von Diagrammen am Laptop" style="background:linear-gradient(120deg,#3f3c38 0%,#8d8a86 30%,#f0f0f0 55%,#d9d4cf 80%,#a9a6a3 100%)"></div>
    <div role="img" aria-label="Fertigungshalle von oben" style="background:radial-gradient(ellipse at 40% 40%,#b58458 0%,rgba(181,132,88,0) 50%),linear-gradient(180deg,#5e4a38,#3a332e)"></div>
    <div role="img" aria-label="Bagger und Schutzhelm im Sonnenuntergang" style="background:radial-gradient(ellipse at 30% 70%,#f3c03a 0%,rgba(243,192,58,0) 35%),linear-gradient(180deg,#f0b45a 0%,#d5843a 45%,#7b5334 80%,#4e3a2a 100%)"></div>
    <div role="img" aria-label="Baustelle mit Kränen vor Stadtkulisse" style="background:linear-gradient(180deg,#dbe8f3 0%,#b6c8d6 45%,#8e9fa8 65%,#7a8a6e 85%,#5f6d58 100%)"></div>
  </div>

  <footer class="footer abs">
    <div class="brand">
      <div class="brand-square"></div>
      <div>
        <div class="brand-name">KLR</div>
        <div class="brand-sub">KLR SERVICES GMBH</div>
      </div>
    </div>
    <div class="footer-links"><span>Impressum</span><span>AGB</span><span>Datenschutz</span><span>Nachhaltigkeit</span></div>
  </footer>
  <div class="copyright abs">© KLR services GmbH</div>

</div>
</body>
</html>
```